Boutique custom software development company needs new business card

Our nearly 20 year old custom software development company would like to better include the fact that we are now providing Bitcoin services. These new services are B2B include education (how to acquire and securely hold Bitcoin) and integrating Bitcoin payments into existing ecommerce sites or other existing systems. Please keep the card clean and simple. Attached is our current design and some other files. vextorial.com

Target Market(s)

businesses owners interested in long term relationship

Industry/Entity Type

Custom software development and Bitcoin

Contact Information for Business Card

Dale Parker, dale@vextorial.com, vextorial.com, (888) 555-VXTRL

Font styles to use
Other font styles liked:
• monospace

Requirements
Must have
• double-sided
Nice to have
• clean and simple
Should not have
• physical address

```html
<!DOCTYPE html>
<html lang="en">
<head>
<meta charset="utf-8">
<title>Vextorial Business Card</title>
<link href="https://fonts.googleapis.com/css2?family=Roboto+Mono:wght@400;700&family=Lato:wght@400&display=swap" rel="stylesheet">
<style>
  :root {
    --stage: #8b7358;
    --card: #141a47;
    --blue: #3f74bd;
    --blue-text: #3d6ab0;
    --orange: #ee7d22;
    --light: #f2f2f2;
  }
  * { margin: 0; padding: 0; box-sizing: border-box; }
  html, body { width: 900px; height: 1200px; overflow: hidden; }
  body { background: var(--stage); position: relative; font-family: "Roboto Mono", monospace; }

  .card {
    position: absolute; left: 78px; width: 744px; height: 442px;
    background: var(--card); border-radius: 26px;
  }
  .card-front { top: 130px; }
  .card-back { top: 638px; }

  .wordmark { position: absolute; font-family: "Roboto Mono", monospace; font-weight: 700; color: var(--blue); line-height: 1; white-space: nowrap; }
  .tagline { position: absolute; font-family: "Lato", sans-serif; color: var(--blue-text); letter-spacing: -0.5px; line-height: 1; white-space: nowrap; }

  .card-front .wordmark { left: 30px; top: 24px; font-size: 63px; }
  .card-front .tagline { left: 44px; top: 107px; font-size: 23px; }

  .brand-square { position: absolute; left: 546px; top: 30px; width: 169px; height: 175px; background: var(--blue); }

  .name-bar { position: absolute; left: 0; top: 255px; width: 15px; height: 52px; background: var(--orange); }
  .person-name { position: absolute; left: 29px; top: 250px; font-size: 28px; font-weight: 700; color: var(--orange); letter-spacing: 1px; }
  .person-title { position: absolute; left: 29px; top: 289px; font-size: 15px; color: var(--light); letter-spacing: 0.5px; }
  .title-rule { position: absolute; left: 189px; top: 299px; width: 526px; height: 2px; background: var(--orange); }

  .contact-list { position: absolute; left: 27px; top: 347px; list-style: none; }
  .contact-list li { display: flex; align-items: center; height: 25px; font-size: 15px; color: var(--light); }
  .contact-list svg { width: 15px; height: 15px; margin-right: 7px; fill: var(--orange); }

  .services { position: absolute; right: 29px; top: 350px; text-align: right; font-size: 15px; line-height: 25px; color: var(--light); list-style: none; }

  .card-back .wordmark { left: 0; width: 744px; text-align: center; top: 120px; font-size: 122px; }
  .card-back .tagline { left: 0; width: 744px; text-align: center; top: 276px; font-size: 42px; }
</style>
</head>
<body>
  <section class="card card-front">
    <div class="wordmark">VEXTORIAL</div>
    <div class="tagline">developer of custom applications</div>
    <div class="brand-square"></div>

    <div class="name-bar"></div>
    <div class="person-name">Dale Parker</div>
    <div class="person-title">Founding Partner</div>
    <div class="title-rule"></div>

    <ul class="contact-list">
      <li>
        <svg viewBox="0 0 16 16" aria-hidden="true"><path d="M3 6c0-2 2-3 5-3s5 1 5 3l-2 1-1-2H6L5 7 3 6zm2 2h6l2 6H3l2-6zm3 1.5a1.8 1.8 0 1 0 0 3.6 1.8 1.8 0 0 0 0-3.6z"/></svg>
        (888) 555-VXTRL
      </li>
      <li>
        <svg viewBox="0 0 16 16" aria-hidden="true"><path d="M1 3h14v1L8 9 1 4V3zm0 3l7 5 7-5v7H1V6z"/></svg>
        dale@vextorial.com
      </li>
      <li>
        <svg viewBox="0 0 16 16" aria-hidden="true"><circle cx="8" cy="8" r="7"/><path d="M8 1v14M1 8h14" stroke="#141a47" stroke-width="1.2" fill="none"/></svg>
        www.vextorial.com
      </li>
    </ul>

    <ul class="services">
      <li>Custom software</li>
      <li>Bitcoin education</li>
      <li>&amp; payment integration</li>
    </ul>
  </section>

  <section class="card card-back">
    <div class="wordmark">VEXTORIAL</div>
    <div class="tagline">developer of custom applications</div>
  </section>
</body>
</html>
```